Harlow Denatl Laboratory nees a window design

We want to make a window cover 8 feet wide and 6 feet tall to advertise our dental lab with all the products we produce<br/>: Digital Cad/Cam<br/>: Implants<br/>: Dentures<br/>: Cast Partials <br/>: Orthodontic appliances<br/><br/> and it has to include a service we provide for a denturist on site by appointment only.<br/><br/>Please use the sample logo below our colours are white backround and blue letters

Font styles to use
Script

Colors
ffffff
0355a3

Requirements
Nice to have
• a picture of a teddy bear on a dental chair, or some dental work particularly bridge work since our moto is Building bridges since 1976
Should not have
• real people

```html
<!DOCTYPE html>
<html lang="en">
<head>
<meta charset="utf-8">
<title>Harlow Denatl Laboratory – Window Banner</title>
<link rel="stylesheet" href="https://fonts.googleapis.com/css2?family=Crimson+Text:ital,wght@0,700;1,400&display=swap">
<style>
  :root {
    --stage: #231f20;
    --paper: #ffffff;
    --brand-blue: #0355a3;
    --brand-blue-deep: #0a4a8e;
    --name-blue: #1a86cf;
    --text-blue: #0d4f9f;
    --chair-light: #7cc3ec;
    --chair-mid: #5fb0e3;
    --chair-base: #e4e6ea;
  }
  * { margin: 0; padding: 0; box-sizing: border-box; }
  html, body {
    width: 1200px;
    height: 1200px;
    overflow: hidden;
    background: var(--stage);
  }
  .banner {
    position: absolute;
    left: 51px;
    top: 327px;
    width: 1097px;
    height: 548px;
    background: var(--paper);
    overflow: hidden;
    font-family: "Crimson Text", Georgia, serif;
  }
  .banner__shapes {
    position: absolute;
    inset: 0;
    width: 100%;
    height: 100%;
  }
  .banner__photo {
    position: absolute;
    left: 46px;
    top: 62px;
    width: 412px;
    height: 432px;
    border-radius: 40px 60px 30px 40px;
    background: linear-gradient(150deg, var(--chair-light) 0%, var(--chair-mid) 45%, var(--chair-base) 100%);
    opacity: 0.9;
  }
  .brand-name {
    position: absolute;
    left: 440px;
    top: 62px;
    width: 600px;
    text-align: center;
    color: var(--name-blue);
    font-weight: 700;
    line-height: 1;
  }
  .brand-name__main {
    display: block;
    font-size: 82px;
    letter-spacing: 3px;
  }
  .brand-name__sub {
    display: block;
    margin-top: 6px;
    font-size: 34px;
    letter-spacing: 2px;
  }
  .services {
    position: absolute;
    left: 500px;
    top: 232px;
    width: 580px;
    text-align: center;
    color: var(--text-blue);
    font-weight: 700;
    font-size: 41px;
    line-height: 52px;
    letter-spacing: -0.5px;
  }
  .appointment {
    position: absolute;
    left: 523px;
    top: 427px;
    width: 433px;
    height: 66px;
    border-radius: 33px;
    background: linear-gradient(90deg, var(--brand-blue-deep), var(--brand-blue));
    color: var(--paper);
    text-align: center;
    padding-top: 3px;
  }
  .appointment__title {
    display: block;
    font-weight: 700;
    font-size: 36px;
    line-height: 36px;
  }
  .appointment__note {
    display: block;
    font-style: italic;
    font-weight: 400;
    font-size: 20px;
    line-height: 22px;
    letter-spacing: 1px;
  }
</style>
</head>
<body>
  <main class="banner">
    <svg class="banner__shapes" viewBox="0 0 1097 548" aria-hidden="true">
      <polygon fill="var(--brand-blue)" points="0,74 40,38 572,548 0,548"/>
      <polygon fill="var(--brand-blue)" points="958,0 1097,0 1097,74 1067,102"/>
    </svg>

    <div class="banner__photo" role="img" aria-label="Teddy bear sitting in a light blue dental chair"></div>

    <h1 class="brand-name">
      <span class="brand-name__main">HARLOW</span>
      <span class="brand-name__sub">DENATL LABORATORY</span>
    </h1>

    <p class="services">
      DIGITAL CAD | IMPLANTS |<br>
      DENTURES | CAST PARTIALS |<br>
      ORTHODONTIC APPLIANCES
    </p>

    <div class="appointment">
      <span class="appointment__title">DENTURIST :</span>
      <span class="appointment__note">ON SITE BY APPOINTMENT ONLY</span>
    </div>
  </main>
</body>
</html>
```